Company identity deisgn should support 2 languages

I would like to get our company identity design
This includes the following only
Business Cards 2 languages Arabic and English
Email signature
Letterhead
Linkedin profile images
Attached is the logo in Ai format

Requirements
Must have
• For business card
Must have
Name and Adrees in arabic
Name and Address in english
You might use both side of the card
Should not have
• Any pictures other than the logo

```html
<!DOCTYPE html>
<html lang="en">
<head>
<meta charset="utf-8">
<title>Lumen Vector Systems – Letterhead</title>
<link href="https://fonts.googleapis.com/css2?family=Questrial&family=Montserrat:wght@500&family=Tajawal:wght@400&display=swap" rel="stylesheet">
<style>
  :root {
    --brand-blue: #1176bc;
    --band-grey: #6d6e71;
    --ink: #231f20;
    --muted: #4a4a4a;
    --paper: #ffffff;
    --backdrop: #e6e6e6;
  }
  * { margin: 0; padding: 0; box-sizing: border-box; }
  html, body { width: 960px; height: 1200px; overflow: hidden; background: var(--backdrop); }
  .letterhead {
    position: absolute; left: 52px; top: 0;
    width: 855px; height: 1200px;
    background: var(--paper);
    font-family: "Questrial", "Century Gothic", sans-serif;
    color: var(--ink);
  }
  .brand {
    position: absolute; left: 215px; top: 74px; width: 400px;
    display: flex; align-items: center; gap: 14px;
    color: var(--brand-blue);
    font-family: "Montserrat", sans-serif; font-weight: 500;
  }
  .brand-dot { width: 52px; height: 52px; border-radius: 50%; background: var(--brand-blue); flex: none; }
  .brand-name { font-size: 23px; letter-spacing: 0.5px; line-height: 1.25; }
  .brand-name .ar { display: block; font-family: "Tajawal", sans-serif; font-size: 15px; letter-spacing: 0; }
  .salutation { position: absolute; left: 79px; top: 352px; font-size: 21px; }
  .body-copy { position: absolute; left: 79px; top: 416px; width: 704px; font-size: 12.3px; line-height: 18.3px; }
  .body-copy p { margin-bottom: 18.3px; }
  .closing { position: absolute; left: 79px; top: 800px; font-size: 12.3px; }
  .signature { position: absolute; left: 79px; top: 846px; width: 112px; height: 64px; background: #ececec; border-radius: 4px; }
  .contact-list { position: absolute; left: 45px; top: 1048px; list-style: none; font-size: 13px; color: var(--muted); }
  .contact-list li { display: flex; align-items: center; gap: 10px; height: 17.3px; }
  .contact-list svg { width: 12px; height: 12px; fill: var(--brand-blue); }
  .address { position: absolute; right: 50px; top: 1030px; text-align: right; font-size: 13px; color: var(--muted); line-height: 17.5px; }
  .address .ar { font-family: "Tajawal", sans-serif; font-size: 14px; line-height: 24px; }
  .address .en { margin-top: 8px; }
  .footer-band { position: absolute; left: 0; top: 1142px; width: 855px; height: 28px; }
  .footer-url {
    position: absolute; left: 0; top: 1142px; width: 740px; height: 28px;
    display: flex; align-items: center; justify-content: center;
    color: #fff; font-size: 12.5px; letter-spacing: 3.2px;
  }
</style>
</head>
<body>
<main class="letterhead">
  <header class="brand">
    <span class="brand-dot"></span>
    <span class="brand-name">LUMEN VECTOR SYSTEMS
      <span class="ar" lang="ar" dir="rtl">شركة لومن فكتور للأنظمة</span>
    </span>
  </header>

  <h1 class="salutation" style="font-weight:400">Dear Mr. Harlow,</h1>

  <section class="body-copy">
    <p>Lorem ipsum dolor sit amet, consectetur adipiscing elit. Donec orci purus, luctus vitae dignissim eu, iaculis sed purus. Vivamus faucibus, ipsum nec aliquet viverra, leo mauris condimentum ligula, sit amet sagittis enim ligula quis arcu. Nam egestas tortor id nisi porttitor mattis. In tortor ante, ultricies in suscipit a, tempus non massa. Vivamus et auctor mi. Fusce vel massa nulla. Phasellus nec eros mauris, et scelerisque orci.</p>
    <p>Donec malesuada orci vitae nulla accumsan porta a id massa. Quisque accumsan iaculis magna sit amet fringilla. Maecenas consequat, magna eget tincidunt semper, odio nibh rutrum mi, id feugiat ante nisi eu risus. Vestibulum nunc orci, rhoncus a placerat in, ultricies in mi. Cras mattis varius eros, vel fringilla nisi suscipit eget. Quisque scelerisque sagittis nulla at porttitor.</p>
    <p>Sed id augue vitae urna euismod commodo aliquet a quam. Pellentesque arcu velit, cursus et malesuada ut, consequat et diam. Nullam erat sem, rhoncus id ullamcorper vitae, rhoncus et arcu. In ultricies ultricies nulla, ut rutrum nisi iaculis at. Donec eu magna a metus ornare faucibus. Fusce aliquet faucibus ultricies. Morbi semper, est id tincidunt gravida, sem arcu adipiscing lacus, ac bibendum nulla leo eu purus. Quisque nec diam sed risus consectetur a ccumsan quis quis nibh. Vestibulum id purus lorem.</p>
    <p>It is a long established fact that a reader will be distracted by the readable content of a page when looking at its layout. The point of using Lorem Ipsum is that it has a more-or-less normal distribution of letters, as opposed to using 'Content here, content here', making it look like readable English. Many desktop publishing packages</p>
  </section>

  <p class="closing">Sincerely,</p>
  <div class="signature" role="img" aria-label="Handwritten signature of the sender"></div>

  <ul class="contact-list">
    <li><svg viewBox="0 0 12 12"><path d="M2.5 0.5 L4.5 0.5 L5.3 3 L4 4.2 C4.8 5.8 6.2 7.2 7.8 8 L9 6.7 L11.5 7.5 L11.5 9.5 C11.5 10.6 10.6 11.5 9.5 11.5 C4.5 11.2 0.8 7.5 0.5 2.5 C0.5 1.4 1.4 0.5 2.5 0.5 Z"/></svg>555-201-4417</li>
    <li><svg viewBox="0 0 12 12"><path d="M3 0 H9 A1 1 0 0 1 10 1 V11 A1 1 0 0 1 9 12 H3 A1 1 0 0 1 2 11 V1 A1 1 0 0 1 3 0 Z M3.4 1.5 V9.5 H8.6 V1.5 Z"/></svg>555-318-6602</li>
    <li><svg viewBox="0 0 12 12"><path d="M3 0 H9 V3 H3 Z M0.5 4 H11.5 V9 H9.5 V7 H2.5 V9 H0.5 Z M3 8 H9 V12 H3 Z"/></svg>555-742-0931</li>
    <li><svg viewBox="0 0 12 12"><path d="M0.5 2.5 H11.5 V9.5 H0.5 Z M1.2 3 L6 6.6 L10.8 3" /></svg>hello@lumenvector.com</li>
  </ul>

  <address class="address" style="font-style:normal">
    <div class="ar" lang="ar" dir="rtl">412 طريق سيدار هولو</div>
    <div class="ar" lang="ar" dir="rtl">بيلمونت، أوريغون 97219</div>
    <div class="en">412 Cedar Hollow Road<br>Bellmont, Oregon 97219</div>
  </address>

  <svg class="footer-band" viewBox="0 0 855 28" preserveAspectRatio="none" aria-hidden="true">
    <rect x="0" y="0" width="855" height="28" fill="var(--band-grey)"/>
    <polygon points="0,0 706,0 696,28 0,28" fill="var(--brand-blue)"/>
  </svg>
  <div class="footer-url">WWW.LUMENVECTOR.COM</div>
</main>
</body>
</html>
```